Crale Electrical Solar Energy Marketing Flyer

Seeking a flyer to market our electrical business - promoting solar energy systems. Will be used as print marketing.

Attached are similar examples in the industry, as well as current Crale Electrical ads and our new "Crale Electrical, Air & Solar" logo.

We would like the reverse side to have information relating to solar for business.

This flyer is to promote the solar arm of our business, however we also deliver electrical and air-conditioning services. If possible it would be great to have a small reference to our air-conditioning service on the front page.We also need to reference the we have finance available.
Updates

Project Deadline Extended Reason: Apologies - due to illness I had been unable to complete the required text copy for flyer. Please note any slight changes to brief and copy will be updated urgently today while I am back in the office. There are some great flyers catching our eye. Added Monday, July 18, 2016

Target Market(s)

Home and Business Owners

Industry/Entity Type

Solar Energy

Logo Text

Crale Electrical, Air & Solar

Requirements
Must have
• Company logo, WPD installer logo, Lumivar Logo, phone number and all licences stated on the attached Crale Electrical ad. Catchy, uncomplicated appearance. Colours and pics to compliment logo. Disclaimer
Nice to have
• Testimonial

```html
<!DOCTYPE html>
<html lang="en">
<head>
<meta charset="utf-8">
<title>Crale Electrical – Solar Flyer</title>
<link rel="stylesheet" href="https://fonts.googleapis.com/css2?family=Oswald:wght@400;500&family=Roboto+Condensed:wght@700&family=Lato:wght@400;700;900&display=swap">
<style>
  :root{
    --red:#c8102e;
    --red-dark:#8e0d1a;
    --blue:#1f7fd1;
    --blue-light:#2aa6e8;
    --navy:#1d3f9e;
    --ink:#111;
    --white:#fff;
    --stage:#2f2a27;
    --orange:#f08a24;
    --grey:#333;
  }
  *{box-sizing:border-box;margin:0;padding:0}
  html,body{width:1200px;height:900px;overflow:hidden}
  body{background:var(--stage);font-family:"Lato",sans-serif;position:relative}
  .flyer{position:absolute;width:537px;height:753px;background:var(--white);overflow:hidden}
  .flyer--front{left:60px;top:62px}
  .flyer--back{left:620px;top:62px;height:751px}
  .flyer svg.shapes{position:absolute;left:0;top:0}
  .abs{position:absolute}

  .brand{display:flex;align-items:center;gap:8px;color:var(--navy);font-weight:900}
  .brand__dot{width:42px;height:42px;border-radius:50%;background:var(--red);flex:none}
  .brand__name{font-size:38px;line-height:.9}
  .brand__tag{font-size:10.5px;line-height:1.2;display:block}

  .headline{font-family:"Roboto Condensed",sans-serif;font-weight:700;text-transform:uppercase;line-height:1}
  .say-no{left:24px;top:132px;font-size:46px;color:var(--red)}
  .to-rising{left:24px;top:178px;font-size:33px;color:var(--blue)}
  .power-bills{left:24px;top:214px;font-size:24px;color:var(--ink)}

  .finance{left:0;top:270px;width:185px;color:var(--white);text-align:center}
  .finance__amount{position:absolute;left:22px;top:8px;font-family:"Lato",sans-serif;font-weight:900;font-size:54px}
  .finance__amount sup{font-size:28px;vertical-align:top;position:relative;top:6px}
  .finance__label{position:absolute;left:98px;top:24px;font-weight:900;font-size:14px;text-align:left;line-height:1.1}
  .finance__label span{color:#ff4b4b;display:block}
  .finance__buy{position:absolute;left:0;width:185px;top:70px;font-weight:700;font-size:14px}
  .lender{position:absolute;left:34px;top:98px;display:flex;align-items:center;gap:8px;font-size:26px;font-weight:400;color:var(--white)}
  .lender__mark{width:18px;height:18px;background:var(--blue-light)}
  .finance__note{position:absolute;left:0;width:185px;top:136px;font-weight:900;font-size:12px}
  .finance__note u{text-decoration:underline}

  .invest{left:250px;top:288px;width:280px;text-align:center;color:var(--white)}
  .invest__title{font-family:"Lato",sans-serif;font-weight:900;font-size:34px;line-height:1.05}
  .invest__title span{font-size:40px;display:block}
  .invest__copy{font-family:"Roboto Condensed",sans-serif;font-weight:700;font-size:13.5px;margin-top:12px;line-height:1.4;white-space:nowrap}

  .quote{left:28px;top:445px;font-family:"Oswald",sans-serif;text-transform:uppercase;line-height:1.1}
  .quote__lead{font-size:27px;color:var(--ink);font-weight:400}
  .quote__main{font-size:34px;color:var(--blue);font-weight:500}

  .contact-front{left:24px;top:530px;color:var(--white)}
  .contact-front__phone{font-family:"Roboto Condensed",sans-serif;font-weight:700;font-size:25px;line-height:1}
  .contact-front__email{font-size:15px;font-weight:700;margin-top:8px}

  .disclaimer{left:24px;top:613px;width:300px;font-size:8.3px;color:var(--grey);line-height:1.35}
  .licences{left:90px;top:672px;width:255px;text-align:right;font-weight:900;font-size:11.5px;line-height:1.45;color:var(--ink);white-space:nowrap}

  .site{font-weight:700;font-size:12px;letter-spacing:3px;color:var(--navy)}
  .site--front{left:0;width:380px;top:713px;text-align:center}
  .site--back{left:0;width:537px;top:706px;text-align:center}

  .reasons{left:14px;top:112px;width:250px;color:var(--white)}
  .reasons__title{font-family:"Oswald",sans-serif;font-size:14px;text-transform:uppercase;margin-bottom:10px}
  .reasons__list{list-style:none;font-size:9.2px;line-height:1.35;font-weight:700;width:225px}
  .reasons__list li{position:relative;padding-left:16px;margin-bottom:10px}
  .reasons__list li::before{content:"";position:absolute;left:0;top:2px;width:9px;height:9px;border-radius:50%;background:var(--white)}

  .business{left:26px;top:270px}
  .business__title{font-size:46px;color:var(--red);letter-spacing:.5px}
  .business__title span{display:block;font-size:31px;margin-top:4px}
  .business__tax{font-size:37px;color:var(--blue);margin-top:12px;text-transform:none}

  .testimonials__tag{left:0;top:443px;width:182px;height:20px;background:var(--blue);color:var(--white);border-radius:0 10px 10px 0;font-weight:900;font-size:13px;padding:2px 0 0 36px;text-transform:uppercase}
  .testimonials__quote{left:30px;top:474px;width:490px;font-size:13.4px;line-height:1.42;color:var(--white);font-weight:700}
  .testimonials__quote cite{font-style:normal;color:var(--blue-light)}

  .contact-back{left:30px;top:604px}
  .contact-back__lead{font-family:"Roboto Condensed",sans-serif;font-weight:700;font-size:25px;color:var(--blue);text-transform:uppercase;line-height:1.1}
  .contact-back__phone{font-family:"Roboto Condensed",sans-serif;font-weight:700;font-size:30px;color:var(--navy);margin-top:2px;line-height:1.1}
  .contact-back__email{font-size:12.5px;color:var(--grey);margin-top:8px}
  .fine-print{left:267px;top:608px;width:250px;font-size:8.5px;color:#555;line-height:1.45}
</style>
</head>
<body>

<section class="flyer flyer--front">
  <svg class="shapes" width="537" height="753" viewBox="0 0 537 753">
    <defs>
      <linearGradient id="skyTone" x1="0" y1="0" x2="0" y2="1">
        <stop offset="0" stop-color="#3d7fd8"/><stop offset=".55" stop-color="#a9c6e6"/><stop offset="1" stop-color="#2c3f78"/>
      </linearGradient>
      <linearGradient id="redPanel" x1="0" y1="0" x2="1" y2="1">
        <stop offset="0" stop-color="#8e0d1a"/><stop offset=".5" stop-color="#c8102e"/><stop offset="1" stop-color="#a50e22"/>
      </linearGradient>
      <linearGradient id="roomTone" x1="0" y1="0" x2="1" y2="1">
        <stop offset="0" stop-color="#f3f5f7"/><stop offset=".6" stop-color="#dfe5ec"/><stop offset="1" stop-color="#7c93b5"/>
      </linearGradient>
    </defs>
    <rect x="0" y="708" width="537" height="24" fill="#2aa6e8"/>
    <g role="img" aria-label="Photo of electricians installing solar panels on a sunny roof">
      <polygon points="300,0 537,0 537,262 190,262" fill="url(#skyTone)"/>
    </g>
    <polygon points="283,0 298,0 188,262 173,262" fill="#1f7fd1"/>
    <polygon points="0,268 180,268 245,440 0,440" fill="#2240a3"/>
    <polygon points="184,268 193,268 258,440 249,440" fill="#2aa6e8"/>
    <polygon points="198,268 537,268 537,440 263,440" fill="url(#redPanel)"/>
    <rect x="0" y="518" width="275" height="82" fill="#c8102e"/>
    <g role="img" aria-label="Photo of a technician in a hard hat fitting an air-conditioning unit">
      <polygon points="248,443 537,443 537,753 398,753" fill="url(#roomTone)"/>
    </g>
    <polygon points="240,443 247,443 397,753 390,753" fill="#c8102e"/>
    <polygon points="230,443 235,443 385,753 380,753" fill="#1f7fd1"/>
  </svg>

  <div class="abs brand" style="left:22px;top:30px">
    <span class="brand__dot"></span>
    <div><span class="brand__name">Crale</span><span class="brand__tag">Electrical, Air &amp; Solar</span></div>
  </div>

  <p class="abs headline say-no">Say No</p>
  <p class="abs headline to-rising">To Rising</p>
  <p class="abs headline power-bills">Power Bills!</p>

  <div class="abs finance" style="height:170px">
    <span class="finance__amount">$0<sup>*</sup></span>
    <span class="finance__label">DEPOSIT<span>FINANCE</span></span>
    <span class="finance__buy">“BUY SOLAR TODAY”</span>
    <span class="lender"><span class="lender__mark"></span>Lumivar</span>
    <span class="finance__note">NO INTEREST <u>EVER!</u></span>
  </div>

  <div class="abs invest">
    <h2 class="invest__title">INVEST<span>IN SOLAR</span></h2>
    <p class="invest__copy">Why not combine your solar install with new<br>air-conditioning or electrical improvements!</p>
  </div>

  <div class="abs quote">
    <p class="quote__lead">Call us for a</p>
    <p class="quote__main">Free Quote</p>
  </div>

  <div class="abs contact-front">
    <p class="contact-front__phone">Call Us: 1300 482 907</p>
    <p class="contact-front__email">dean@craleelectrical.com.au</p>
  </div>

  <p class="abs disclaimer">Continuing credit provided by Lumivar Flexi-Pay Pty Ltd. Fees (including Establishment Fee, Monthly Account Keeping fees and Payment Processing fees), charges, terms, conditions and lending criteria apply. Other deposit amounts may be required depending on purchase. All information correct at time of print. Subject to changes.</p>

  <p class="abs licences">Licence: 58231<br>WPD Accreditation: A0917456</p>

  <p class="abs site site--front">www.craleelectrical.com.au</p>
</section>

<section class="flyer flyer--back">
  <svg class="shapes" width="537" height="751" viewBox="0 0 537 751">
    <defs>
      <linearGradient id="roofTone" x1="0" y1="0" x2="1" y2="1">
        <stop offset="0" stop-color="#5e9be0"/><stop offset=".5" stop-color="#c9d7e8"/><stop offset="1" stop-color="#23407e"/>
      </linearGradient>
      <linearGradient id="reasonBox" x1="0" y1="0" x2="1" y2="0">
        <stop offset="0" stop-color="#1d50b8"/><stop offset="1" stop-color="#2aa6e8"/>
      </linearGradient>
      <linearGradient id="quoteBand" x1="0" y1="0" x2="1" y2="0">
        <stop offset="0" stop-color="#b10f26"/><stop offset=".5" stop-color="#8e0d1a"/><stop offset="1" stop-color="#c8102e"/>
      </linearGradient>
    </defs>
    <g role="img" aria-label="Photo of a worker in a hard hat carrying a solar panel on a rooftop">
      <polygon points="215,0 537,0 537,470" fill="url(#roofTone)"/>
    </g>
    <polygon points="193,0 212,0 537,478 537,512" fill="#c8102e"/>
    <polygon points="178,0 187,0 537,520 537,534" fill="#1f7fd1"/>
    <polygon points="0,100 260,100 300,245 0,245" fill="url(#reasonBox)"/>
    <rect x="0" y="428" width="537" height="142" fill="url(#quoteBand)"/>
    <line x1="235" y1="598" x2="235" y2="690" stroke="#bbb" stroke-width="1"/>
    <circle cx="345" cy="668" r="24" fill="var(--orange)"/>
    <rect x="0" y="700" width="537" height="28" fill="#2aa6e8"/>
  </svg>

  <div class="abs brand" style="left:22px;top:28px">
    <span class="brand__dot"></span>
    <div><span class="brand__name">Crale</span><span class="brand__tag">Electrical, Air &amp; Solar</span></div>
  </div>

  <div class="abs reasons">
    <h3 class="reasons__title">3 reasons to install solar...</h3>
    <ul class="reasons__list">
      <li>The sun provides free, clean energy, and is the best way to save money</li>
      <li>The government provides generous incentives saving you thousands of $$.</li>
      <li>Advancing technology means you can store your energy and use it night.</li>
    </ul>
  </div>

  <div class="abs business headline">
    <h2 class="business__title">Solar for<span>your business</span></h2>
    <p class="business__tax">$20,000 Tax break</p>
  </div>

  <p class="abs testimonials__tag">Testimonials:</p>
  <blockquote class="abs testimonials__quote">“We have been using Dean from Crale Electrical and Trade for over 3 years. We have found Dean to be extremely helpful and willing to go that little bit further to ensure that the job is done properly. Dean has always been competitively priced and the job is completed on time. We wouldn’t recommend anyone else!” - <cite>Harlow Pastoral Co.</cite></blockquote>

  <div class="abs contact-back">
    <p class="contact-back__lead">Call us today:</p>
    <p class="contact-back__phone">1300 482 907</p>
    <p class="contact-back__email">dean@craleelectrical.com.au</p>
  </div>

  <p class="abs fine-print">Finance Available to approved applicants. All information correct at time of print. Subject to changes.</p>

  <p class="abs site site--back">www.craleelectrical.com.au</p>
</section>

</body>
</html>
```